Website for new slot-booking/reservations website/software

For a new software product we need a brand new logo and website for a reservations/booking system. The website should ideally present the main features with information text, contact info, news page as well as registration and pricing pages. As currently primary field of operation the software should be used for tennis but later on, also for other sport types. Also we'd like to be the logo a text-brand which includes the name "zeitfeldo.com" or just "zeitfeldo". The logo should ideally include an icon-design in some way. Generally we are open for ideas.

Bootstrap 4 template is a minimum requirement. (Multi-Page preferred, Single-Page still OK.)

You can use the attached image as an inspiration, but change of colors or other design elements are up to you. Currently the application has a primary color of #5500ff. The website created by you will not include the application itself, so it can have different (but ideally similar) Look&Feel.
Updates

Target Market(s)

Sports, Club-Management

Logo Text

zeitfeldo.com

Coding

Coded - Design and coding required

Number of Pages Required

5+ page

Font styles to use
Sans Serif

Requirements
Must have
• Bootstrap 4 Template, SCSS
Nice to have
• Rapid Loading Times, not too much external JS Libraries.
Should not have
• Extensive animations

```html
<!DOCTYPE html>
<html lang="en">
<head>
<meta charset="utf-8">
<title>Zeitfeldo – A reservations/booking system</title>
<link rel="stylesheet" href="https://fonts.googleapis.com/css2?family=Lato:ital,wght@0,400;0,700;0,900;1,400&family=Oswald:wght@500&display=swap">
<style>
:root{
  --primary:#5500ff;
  --green:#2ba56b;
  --ink:#2e2e2e;
  --text:#555;
  --light:#f3f3f3;
  --white:#fff;
  --footer-bar:#ececec;
}
*{box-sizing:border-box;margin:0;padding:0}
html,body{width:1200px;height:4461px;overflow:hidden}
body{font-family:"Lato",sans-serif;color:var(--ink);background:var(--white);position:relative}
.abs{position:absolute}
.btn{position:absolute;display:flex;align-items:center;justify-content:center;border-radius:22px;font-weight:700;font-size:15px}
.btn-outline{border:2px solid var(--green);color:var(--green);background:var(--white)}
.btn-solid{background:var(--green);color:var(--white)}
/* nav */
.site-nav{position:absolute;left:0;top:0;width:1200px;height:132px;background:var(--white)}
.brand{position:absolute;display:flex;align-items:center;gap:12px;font-weight:900;color:var(--ink)}
.brand-mark{width:44px;height:44px;background:var(--primary)}
.nav-links{position:absolute;left:381px;top:62px;display:flex;gap:34px;font-size:12.5px;font-weight:700;color:#333}
.nav-links .active{color:var(--primary)}
.nav-register{position:absolute;left:911px;top:50px;width:118px;height:38px;border-radius:19px;background:var(--primary);color:#fff;font-size:12.5px;font-weight:700;display:flex;align-items:center;justify-content:center}
.nav-login{position:absolute;left:1035px;top:50px;width:91px;height:38px;border-radius:19px;border:2px solid #333;font-size:12.5px;font-weight:700;display:flex;align-items:center;justify-content:center}
/* hero */
.hero{position:absolute;left:0;top:132px;width:1200px;height:616px;background:linear-gradient(120deg,#2a2f33 0%,#545a5f 45%,#3b3f42 70%,#1e2225 100%)}
.hero h1{position:absolute;left:74px;top:190px;font-size:66px;font-weight:900;color:#fff;letter-spacing:1px}
.hero .tagline{position:absolute;left:74px;top:272px;font-size:32px;color:#fff}
.dots{position:absolute;left:560px;top:561px;display:flex;gap:11px}
.dots span{width:11px;height:11px;border-radius:50%;background:#fff}
.dots span:first-child{background:#2f7de0}
/* sections */
.center{position:absolute;left:0;width:1200px;text-align:center}
.section-title{font-size:48px;font-weight:700}
.lead{color:var(--primary);font-weight:700;font-size:18px}
.para{font-size:14px;line-height:23px;color:var(--text)}
.features{position:absolute;left:0;top:1148px;width:1200px;height:431px;background:var(--primary);color:#fff}
.feature{position:absolute;top:150px;width:250px;text-align:center}
.feature .ring{width:86px;height:86px;border:2px solid #fff;border-radius:50%;margin:0 auto;display:flex;align-items:center;justify-content:center}
.feature h3{font-size:22px;font-weight:700;margin-top:22px}
.feature p{font-size:13.5px;line-height:27px;margin-top:4px;opacity:.9}
.photo-circle{position:absolute;width:420px;height:420px;border-radius:50%}
.row-title{position:absolute;font-size:26px;line-height:35px;font-weight:700;color:var(--primary)}
.row-text{position:absolute;width:550px;font-size:13.5px;line-height:27.5px;color:var(--text)}
.pricing{position:absolute;left:0;top:2597px;width:1200px;height:686px;background:linear-gradient(135deg,#1a3f47 0%,#215652 35%,#17304a 70%,#0f1c40 100%)}
.plan{position:absolute;background:var(--light);text-align:center}
.plan h4{color:var(--primary);font-size:18px;font-weight:700}
.price{font-family:"Oswald",sans-serif;color:var(--green);font-size:44px;font-weight:500;line-height:1}
.price sup{font-size:20px;vertical-align:top;position:relative;top:6px}
.price small{font-size:26px}
.per{font-family:"Oswald",sans-serif;font-size:19px;color:#444;margin-top:4px}
.plan ul{list-style:none;text-align:left;margin:40px 0 0 28px;font-size:14px;color:#444}
.plan li{display:flex;align-items:center;gap:18px;height:29.5px}
.news-img{position:absolute;width:243px;height:225px;border-radius:4px}
.news-title{position:absolute;font-size:21px;line-height:27px;font-weight:700;color:var(--primary)}
.news-text{position:absolute;width:230px;font-size:13.5px;line-height:26px;color:var(--text)}
.contact{position:absolute;left:0;top:3758px;width:1200px;height:386px}
.contact-card{position:absolute;left:74px;top:57px;width:373px;height:273px;background:#fff;border-radius:10px}
.footer{position:absolute;left:0;top:4144px;width:1200px;height:244px;background:#fff}
.footer h5{position:absolute;font-size:15px;font-weight:700}
.footer .links{position:absolute;font-size:13px;line-height:28px;color:#444}
.footer-bar{position:absolute;left:0;top:4388px;width:1200px;height:73px;background:var(--footer-bar);font-size:12px;color:#555}
.social{position:absolute;top:28px;width:18px;height:18px;border-radius:50%;background:#666}
</style>
</head>
<body>

<header class="site-nav">
  <div class="brand" style="left:60px;top:44px;font-size:32px"><span class="brand-mark"></span>Zeitfeldo</div>
  <nav class="nav-links">
    <span class="active">HOME</span><span>ABOUT US</span><span>PRODUCTS</span><span>NEWS</span><span>PRICING</span><span>CONTACT</span>
  </nav>
  <div class="nav-register">REGISTER</div>
  <div class="nav-login">LOG IN</div>
</header>

<section class="hero" role="img" aria-label="Photo of hands using a laptop showing a tennis court booking app">
  <h1>Zeitfeldo</h1>
  <p class="tagline">A reservations/booking system</p>
  <div class="btn btn-solid" style="left:76px;top:346px;width:176px;height:42px">Request Demo</div>
  <div class="dots"><span></span><span></span><span></span><span></span></div>
</section>

<section class="about">
  <h2 class="center section-title" style="top:795px">Who We Are</h2>
  <p class="center lead" style="top:876px">Sed ut perspiciatis unde omnis iste natus error sit voluptatem accusantium doloremque</p>
  <p class="para" style="position:absolute;left:100px;top:918px;width:1000px;text-align:center">Nemo enim ipsam voluptatem quia voluptas sit aspernatur aut odit aut fugit, sed quia consequuntur magni dolores eos qui ratione voluptatem sequi nesciunt. Neque porro quisquam est, qui dolorem ipsum quia dolor sit amet, consectetur, adipisci velit, sed quia non numquam eius modi tempora incidunt ut labore et dolore magnam aliquam quaerat voluptatem.</p>
  <div class="btn btn-outline" style="left:512px;top:1028px;width:177px;height:44px">Read More</div>
</section>

<section class="features">
  <h2 class="center section-title" style="top:48px;color:#fff">Features</h2>
  <div class="feature" style="left:70px">
    <div class="ring"><svg width="34" height="28" viewBox="0 0 34 28" fill="none" stroke="#fff" stroke-width="2.5"><rect x="5" y="3" width="24" height="16"/><path d="M1 24h32"/></svg></div>
    <h3>Voluptas Nulla</h3><p>Nemo enim ipsam voluptatem quia voluptas sit aspernatur aut odit aut fugit consequuntur.</p>
  </div>
  <div class="feature" style="left:340px">
    <div class="ring"><svg width="30" height="36" viewBox="0 0 30 36" fill="none" stroke="#fff" stroke-width="2.5"><path d="M15 2 3 7v10c0 8 5 14 12 17 7-3 12-9 12-17V7z"/><path d="M15 8v21c4-2 7-6 7-11V11z" fill="#fff"/></svg></div>
    <h3>Voluptas Nulla</h3><p>Nemo enim ipsam voluptatem quia voluptas sit aspernatur aut odit aut fugit consequuntur.</p>
  </div>
  <div class="feature" style="left:610px">
    <div class="ring"><svg width="36" height="30" viewBox="0 0 36 30" fill="none" stroke="#fff" stroke-width="2.5"><path d="M2 2v26h32"/><path d="M9 24v-8M15 24V10M21 24v-6M27 24V6" stroke-width="3"/></svg></div>
    <h3>Voluptas Nulla</h3><p>Nemo enim ipsam voluptatem quia voluptas sit aspernatur aut odit aut fugit consequuntur.</p>
  </div>
  <div class="feature" style="left:880px">
    <div class="ring"><svg width="38" height="38" viewBox="0 0 38 38" fill="none" stroke="#fff" stroke-width="3"><path d="M31 14A13 13 0 0 0 7 12"/><path d="M7 24a13 13 0 0 0 24 2"/><path d="M31 5v9h-9M7 33v-9h9"/></svg></div>
    <h3>Voluptas Nulla</h3><p>Nemo enim ipsam voluptatem quia voluptas sit aspernatur aut odit aut fugit consequuntur.</p>
  </div>
</section>

<section class="detail-rows">
  <div class="photo-circle" style="left:76px;top:1643px;background:radial-gradient(circle at 45% 40%,#8c98a3,#4d4a45 60%,#6b4a34)" role="img" aria-label="Photo of a laptop and phone showing a booking calendar"></div>
  <h3 class="row-title" style="left:556px;top:1697px">Nam libero tempore, cum soluta nobis<br>est eligendi optio cumque</h3>
  <p class="row-text" style="left:556px;top:1787px">Aliquam molestie, mi et imperdiet euismod, dui purus auctor tellus, et interdum lacus lectus et ante. Sed accumsan sollicitudin sapien, sit amet adipiscing turpis gravida ac. In congue, neque ac lobortis volutpat, libero mauris varius mi, vitae suscipit ipsum ligula vitae risus. Duis aliquam nibh a dui iaculis viverra a velitcommodo.</p>
  <div class="btn btn-outline" style="left:556px;top:1957px;width:179px;height:42px">Read More</div>

  <h3 class="row-title" style="left:106px;top:2156px">Nam libero tempore, cum soluta nobis<br>est eligendi optio cumque</h3>
  <p class="row-text" style="left:106px;top:2246px">Aliquam molestie, mi et imperdiet euismod, dui purus auctor tellus, et interdum lacus lectus et ante. Sed accumsan sollicitudin sapien, sit amet adipiscing turpis gravida ac. In congue, neque ac lobortis volutpat, libero mauris varius mi, vitae suscipit ipsum ligula vitae risus. Duis aliquam nibh a dui iaculis viverra a velitcommodo.</p>
  <div class="btn btn-outline" style="left:106px;top:2415px;width:179px;height:42px">Read More</div>
  <div class="photo-circle" style="left:706px;top:2102px;background:radial-gradient(circle at 50% 45%,#b9c0c8,#6f6860 55%,#3a3532)" role="img" aria-label="Photo of a tablet showing a tennis video lesson"></div>
</section>

<section class="pricing">
  <h2 class="center section-title" style="top:62px;color:#fff">Prcing Plans</h2>
  <div class="plan" style="left:208px;top:191px;width:244px;height:389px">
    <h4 style="margin-top:40px">Basic</h4>
    <div class="price" style="margin-top:16px"><sup>$</sup>25<small>.00</small></div><div class="per">p.m</div>
    <ul><li><b>✔</b>Duis aliquam nibh</li><li><b>✔</b>Dui iaculis viverravelit</li><li><b>✔</b>Vivamus faucibus</li><li><b>✔</b>Egestas</li></ul>
    <div class="btn btn-solid" style="left:39px;top:330px;width:166px;height:38px;font-size:14px">More Details</div>
  </div>
  <div class="plan" style="left:466px;top:153px;width:268px;height:427px">
    <h4 style="margin-top:34px">Professional</h4>
    <div class="price" style="margin-top:16px"><sup>$</sup>50<small>.00</small></div><div class="per">p.m</div>
    <ul><li><b>✔</b>Duis aliquam nibh</li><li><b>✔</b>Dui iaculis viverravelit</li><li><b>✔</b>Vivamus faucibus</li><li><b>✔</b>Egestas</li><li><b>✔</b>Nunc consequat</li></ul>
    <div class="btn btn-solid" style="left:51px;top:351px;width:166px;height:38px;font-size:14px">More Details</div>
  </div>
  <div class="plan" style="left:748px;top:191px;width:242px;height:389px">
    <h4 style="margin-top:40px">Standard</h4>
    <div class="price" style="margin-top:16px"><sup>$</sup>45<small>.00</small></div><div class="per">p.m</div>
    <ul><li><b>✔</b>Duis aliquam nibh</li><li><b>✔</b>Dui iaculis viverravelit</li><li><b>✔</b>Vivamus faucibus</li><li><b>✔</b>Egestas</li></ul>
    <div class="btn btn-solid" style="left:39px;top:320px;width:166px;height:38px;font-size:14px">More Details</div>
  </div>
</section>

<section class="news">
  <h2 class="center section-title" style="top:3335px">News</h2>
  <div class="news-img" style="left:74px;top:3444px;background:linear-gradient(135deg,#5a4636,#c9b59c 55%,#3d3128)" role="img" aria-label="Photo of hands holding a phone with an online ticket"></div>
  <h3 class="news-title" style="left:345px;top:3438px">Aliquam molestie, mi et<br>imperdiet euismod,</h3>
  <p class="news-text" style="left:345px;top:3498px">Auctor tellus, et interdum lacus lectus et ante ed accumsan sollicitudin sapien, sit amet adipi scing turpis gravida ac.</p>
  <div class="btn btn-solid" style="left:345px;top:3634px;width:167px;height:38px;font-size:14px">Read More</div>

  <div class="news-img" style="left:615px;top:3444px;background:linear-gradient(135deg,#3a2c24,#7a5d48 50%,#2a3d2a)" role="img" aria-label="Photo of a person watching sport on a laptop"></div>
  <h3 class="news-title" style="left:885px;top:3438px">Aliquam molestie, mi et<br>imperdiet euismod,</h3>
  <p class="news-text" style="left:885px;top:3498px">Auctor tellus, et interdum lacus lectus et ante ed accumsan sollicitudin sapien, sit amet adipi scing turpis gravida ac.</p>
  <div class="btn btn-solid" style="left:885px;top:3634px;width:167px;height:38px;font-size:14px">Read More</div>
</section>

<section class="contact">
  <div class="abs" style="left:0;top:0;width:343px;height:386px;background:var(--primary)"></div>
  <div class="abs" style="left:343px;top:0;width:857px;height:386px;background:linear-gradient(120deg,#8a98a8,#c4ccd4 45%,#6c7784 75%,#3c4450)" role="img" aria-label="Photo of a developer working at a computer"></div>
  <div class="contact-card">
    <h2 style="position:absolute;left:40px;top:30px;font-size:48px;font-weight:400">Contact Info</h2>
    <p class="abs" style="left:40px;top:100px;font-size:13.5px;color:#333">214 Linden Court, Harrowgate, HG4 2PL</p>
    <p class="abs" style="left:40px;top:130px;font-size:13.5px;color:#333;display:flex;gap:16px;align-items:center">
      <svg width="14" height="14" viewBox="0 0 24 24" fill="#333"><path d="M6.6 10.8a15 15 0 0 0 6.6 6.6l2.2-2.2a1 1 0 0 1 1-.25 11.4 11.4 0 0 0 3.6.57 1 1 0 0 1 1 1V20a1 1 0 0 1-1 1A17 17 0 0 1 3 4a1 1 0 0 1 1-1h3.5a1 1 0 0 1 1 1c0 1.25.2 2.45.57 3.57a1 1 0 0 1-.25 1z"/></svg>1-800-555-0142</p>
    <p class="abs" style="left:40px;top:159px;font-size:13.5px;color:#333;display:flex;gap:16px;align-items:center">
      <svg width="14" height="12" viewBox="0 0 24 20" fill="#333"><path d="M0 2h24v2L12 11 0 4z M0 7l12 7 12-7v13H0z"/></svg>info@zeitfeldo.com</p>
    <div class="btn btn-outline" style="left:33px;top:208px;width:176px;height:42px">Contact Us</div>
  </div>
</section>

<footer class="footer">
  <div class="brand" style="left:62px;top:42px;font-size:32px"><span class="brand-mark"></span>Zeitfeldo</div>
  <p class="abs" style="left:62px;top:110px;width:335px;font-size:13px;line-height:22.5px;color:#333">Aliquam molestie, mi et imperdiet euismod, dui purus auctor tellus, et interdum lacus lectus et ante. Sed accumsan sollicitudin sapien, sit amet adipiscing turpis gravida ac.</p>
  <h5 style="left:448px;top:54px">Company</h5>
  <div class="links" style="left:448px;top:92px">Home<br>About<br>Products<br>Features</div>
  <div class="links" style="left:548px;top:92px">Pricing<br>News<br>Contact Us</div>
  <h5 style="left:683px;top:54px">Resources</h5>
  <div class="links" style="left:683px;top:92px">Duis aliquam nibh<br>Dui iaculis<br>Viverra id a velit<br>Vivamus egestas</div>
  <h5 style="left:856px;top:54px">Subscribe Our Newsletter</h5>
  <p class="abs" style="left:856px;top:82px;width:280px;font-size:12.5px;line-height:22px;font-style:italic;color:#333">Aliquam molestie, mi et imperdiet euismod, dui purus auctor tellus</p>
  <div class="abs" style="left:856px;top:143px;width:270px;height:40px;border:1px solid #ccc;border-radius:20px;font-size:12px;color:#777;padding:12px 0 0 20px">Enter Email Address</div>
  <div class="abs" style="left:1075px;top:143px;width:51px;height:40px;border-radius:0 20px 20px 0;background:var(--green);color:#fff;font-weight:700;font-size:14px;display:flex;align-items:center;justify-content:center">GO</div>
</footer>

<div class="footer-bar">
  <p class="abs" style="left:74px;top:30px">Copyright © 2021. Company Name. All Rihgt Reserved</p>
  <span class="social" style="left:952px"></span><span class="social" style="left:988px"></span><span class="social" style="left:1028px"></span><span class="social" style="left:1068px"></span><span class="social" style="left:1107px"></span>
</div>

</body>
</html>
```